web page design with coding

We are a start up insurance agency who needs to design a full functional web page. we recently did a postcard design though drawkettle I will upload the final project for you to see the color scheme/font we would like to continue to use. I also have a rough draft of verbage I would like our website to have. I will upload that as well.

Reason: I am sorry but the person who will make the final decision on the website is out of the country at the moment and will make the final decision when he returns.

Industry/Entity Type

Insurance

Coding

Coded - Design and coding required

```html
<!DOCTYPE html>
<html lang="en">
<head>
<meta charset="utf-8">
<title>Meridian Shield Insurance</title>
<link href="https://fonts.googleapis.com/css2?family=Open+Sans:wght@400;600;700&display=swap" rel="stylesheet">
<style>
:root{
  --green:#2e7d3e;
  --green-bright:#2f8a42;
  --navy:#1b3a6b;
  --navy-deep:#163a6e;
  --blue:#23508a;
  --ink:#3c3c3c;
  --muted:#777;
  --dark:#262829;
  --footer:#1c3f78;
  --white:#fff;
}
*{box-sizing:border-box;margin:0;padding:0}
html,body{width:1200px;height:2206px;overflow:hidden}
body{font-family:"Open Sans",Arial,sans-serif;color:var(--ink);background:var(--white);position:relative}
.abs{position:absolute}

/* header */
.topline{left:0;top:0;width:1200px;height:4px;background:var(--green)}
.header{left:0;top:4px;width:1200px;height:128px;background:var(--white)}
.brand{left:97px;top:36px;font-size:30px;font-weight:700;color:var(--navy);letter-spacing:1px;line-height:1}
.brand-sub{left:97px;top:76px;font-size:12px;font-weight:600;color:var(--navy)}
.btn-sm{top:25px;width:94px;height:31px;font-size:10px;font-weight:600;color:var(--white);text-align:center;line-height:31px;border-radius:2px}
.btn-login{left:904px;background:var(--navy)}
.btn-register{left:1007px;background:var(--green-bright)}
.nav{top:82px;font-size:12px;font-weight:600;color:#444;letter-spacing:.3px}
.nav.active{color:var(--green)}

/* hero */
.hero{left:0;top:132px;width:1200px;height:634px}
.hero-photo{left:0;top:132px;width:1200px;height:634px;background:linear-gradient(100deg,#5a6670 0%,#9aa3a8 35%,#d9dcdc 60%,#c8ccd0 100%)}
.hero-title{left:98px;top:312px;font-size:56px;font-weight:700;color:var(--white);line-height:1}
.hero-text{left:98px;top:386px;width:400px;font-size:13px;line-height:25px;color:var(--white)}
.btn-hero{left:98px;top:470px;width:159px;height:45px;background:var(--navy);color:var(--white);font-size:13px;font-weight:700;line-height:45px;text-align:center;border-radius:2px}
.hero-arrows{left:100px;top:526px}

/* about */
.about-title{left:0;top:814px;width:1200px;text-align:center;font-size:26px;font-weight:700;color:#444;letter-spacing:.5px}
.about-title span{color:var(--navy)}
.about-text{left:155px;top:858px;width:890px;text-align:center;font-size:12.5px;line-height:26px;color:var(--muted)}
.btn-mid{top:953px;height:41px;line-height:41px;text-align:center;color:var(--white);font-size:14px;border-radius:2px}
.btn-read{left:435px;width:152px;background:var(--green-bright)}
.btn-best{left:613px;width:153px;background:var(--navy)}

/* insurance band */
.band-left{left:0;top:1051px;width:603px;height:314px;background:var(--blue)}
.band-right{left:603px;top:1051px;width:597px;height:314px;background:var(--navy-deep)}
.band-title{top:1114px;font-size:22px;font-weight:700;color:var(--white);letter-spacing:.3px}
.band-text{top:1154px;width:470px;font-size:11.5px;line-height:22.5px;color:var(--white)}
.btn-outline{top:1278px;width:130px;height:40px;border:1px solid var(--white);color:var(--white);font-size:13px;line-height:38px;text-align:center}
.notch{left:298px;top:1343px}

/* coverage */
.cov-title{left:0;top:1411px;width:1200px;text-align:center;font-size:26px;font-weight:700;color:#444;letter-spacing:.5px}
.cov-title span{color:var(--navy)}
.cov-sub{left:0;top:1451px;width:1200px;text-align:center;font-size:13px;font-weight:700;color:var(--green);letter-spacing:.8px}
.cov-item{width:210px}
.cov-item h3{font-size:13.5px;font-weight:700;line-height:21px;letter-spacing:.4px;color:var(--green)}
.cov-item h3.navy{color:var(--navy)}
.cov-item p{font-size:11.5px;line-height:22px;color:var(--muted)}
.cov-left{text-align:right}
.icon-circle{width:86px;height:86px;border-radius:50%;background:var(--white)}
.icon-circle.green{border:4px solid var(--green)}
.icon-circle.navy{border:4px solid var(--navy)}
.icon-circle svg{position:absolute;left:21px;top:21px}
.tablet{left:465px;top:1534px;width:267px;height:188px;background:#111;border-radius:8px}
.tablet-screen{left:479px;top:1547px;width:239px;height:156px;background:linear-gradient(180deg,#ffffff,#e8eaee)}
.tablet-name{left:479px;top:1608px;width:239px;text-align:center;font-size:17px;font-weight:700;color:var(--navy)}
.tablet-dot{left:594px;top:1706px;width:9px;height:9px;border-radius:50%;background:#444}

/* contact */
.contact{left:0;top:1790px;width:1200px;height:361px;background:var(--dark)}
.contact-title{left:0;top:1816px;width:1200px;text-align:center;font-size:26px;font-weight:700;color:var(--white);letter-spacing:.5px}
.map{left:98px;top:1890px;width:286px;height:203px;background:linear-gradient(135deg,#e4e6dc,#cfd6e0);border:2px solid #ddd}
.c-icon{width:38px;height:38px;border-radius:50%;border:1px solid #bbb}
.c-icon svg{position:absolute;left:10px;top:10px}
.c-text{left:546px;font-size:13px;line-height:22px;color:#e8e8e8}
.field{left:812px;width:284px;height:35px;background:var(--white);border-radius:2px;font-size:10px;color:#666;line-height:35px;padding-left:34px;letter-spacing:.3px}
.field svg{position:absolute;left:12px;top:11px}
.field.msg{height:61px;line-height:30px}
.btn-send{left:812px;top:2082px;width:131px;height:37px;background:var(--navy);color:var(--white);font-size:13px;font-weight:700;line-height:37px;text-align:center}

/* footer */
.footer{left:0;top:2151px;width:1200px;height:55px;background:var(--footer)}
.footer-text{left:98px;top:2167px;font-size:13px;color:var(--white)}
</style>
</head>
<body>

<div class="abs topline"></div>
<header class="abs header"></header>
<div class="abs brand">MSI</div>
<div class="abs brand-sub">Meridian Shield Insurance</div>
<div class="abs btn-sm btn-login">LOGIN</div>
<div class="abs btn-sm btn-register">REGISTER</div>
<nav>
  <div class="abs nav active" style="left:557px">HOME</div>
  <div class="abs nav" style="left:634px">ABOUT US</div>
  <div class="abs nav" style="left:735px">SERVICES</div>
  <div class="abs nav" style="left:828px">BLOG</div>
  <div class="abs nav" style="left:901px">TESTIMONIALS</div>
  <div class="abs nav" style="left:1026px">CONTACT US</div>
</nav>

<section>
  <div class="abs hero-photo" role="img" aria-label="Photo of smiling clients reviewing insurance documents with an agent at a desk"></div>
  <svg class="abs" style="left:0;top:132px" width="1200" height="634" viewBox="0 0 1200 634">
    <path d="M0 510 Q420 740 1200 410 L1200 634 L0 634 Z" fill="var(--green)"/>
    <path d="M0 505 Q430 720 1200 430 L1200 634 L0 634 Z" fill="var(--navy)"/>
    <path d="M0 530 Q430 740 1200 450 L1200 634 L0 634 Z" fill="var(--green)"/>
    <path d="M0 545 Q450 760 1200 480 L1200 634 L0 634 Z" fill="var(--white)"/>
  </svg>
  <div class="abs hero-title">MSI</div>
  <p class="abs hero-text">Meridian Shield Insurance has joined with regional &amp; national insurance companies to provide quality products and superior service. We take the time to discuss options and</p>
  <div class="abs btn-hero">READ MORE INFO</div>
  <svg class="abs hero-arrows" width="72" height="30" viewBox="0 0 72 30">
    <circle cx="15" cy="15" r="14" fill="rgba(255,255,255,.55)"/>
    <path d="M18 8 L11 15 L18 22" stroke="#fff" stroke-width="3" fill="none"/>
    <circle cx="55" cy="15" r="14" fill="rgba(255,255,255,.55)"/>
    <path d="M52 8 L59 15 L52 22" stroke="#fff" stroke-width="3" fill="none"/>
  </svg>
</section>

<section>
  <h2 class="abs about-title">ABOUT <span>MERIDIAN SHIELD INSURANCE</span></h2>
  <p class="abs about-text">Established in 2015, Meridian Shield Insurance is a full service independent insurance agency. Our licensed agents have the experience to custom tailor a program to meet your specific needs &amp; our professional support staff will provide you with top notch customer service to help ease the burden of managing your insurance program. We have established relationships with carriers</p>
  <div class="abs btn-mid btn-read">Read More Info</div>
  <div class="abs btn-mid btn-best">Best Result</div>
</section>

<section>
  <div class="abs band-left"></div>
  <div class="abs band-right"></div>
  <h2 class="abs band-title" style="left:98px">BUSINESS INSURANCE</h2>
  <p class="abs band-text" style="left:98px">Business insurance is a risk management tool that enables businesses to transfer the risk of a loss to an insurance company. Business insurance protects your business against the possibility of sustaining a much larger financial loss. All businesses need to insure against risks—such as fire, theft, natural disaster, legal liability, automobile accidents, and the death or disability of key employees</p>
  <div class="abs btn-outline" style="left:98px">More Details</div>
  <h2 class="abs band-title" style="left:659px">PERSONAL INSURANCE</h2>
  <p class="abs band-text" style="left:659px">Business insurance is a risk management tool that enables businesses to transfer the risk of a loss to an insurance company. Business insurance protects your business against the possibility of sustaining a much larger financial loss. All businesses need to insure against risks—such as fire, theft, natural disaster, legal liability, automobile accidents, and the death or disability of key employ-</p>
  <div class="abs btn-outline" style="left:659px">More Details</div>
  <svg class="abs notch" width="32" height="22" viewBox="0 0 32 22"><path d="M0 22 L16 0 L32 22 Z" fill="#fff"/></svg>
</section>

<section>
  <h2 class="abs cov-title">BUSINESS <span>INSURANCE COVERAGE</span></h2>
  <div class="abs cov-sub">MERIDIAN SHIELD INSURANCE PROVIDES</div>

  <div class="abs cov-item cov-left" style="left:84px;top:1498px">
    <h3>BUSINESS OWNERS<br>POLICY (BOP)</h3>
    <p>Business insurance is a risk management tool that enables</p>
  </div>
  <div class="abs icon-circle green" style="left:310px;top:1504px">
    <svg width="44" height="44" viewBox="0 0 44 44"><rect x="5" y="13" width="34" height="24" rx="3" fill="var(--green)"/><rect x="16" y="7" width="12" height="8" rx="2" fill="none" stroke="var(--green)" stroke-width="3"/></svg>
  </div>

  <div class="abs cov-item cov-left" style="left:84px;top:1662px">
    <h3 class="navy">COMMERCIAL AUTO</h3>
    <p>Business insurance is a risk management tool that enables</p>
  </div>
  <div class="abs icon-circle navy" style="left:310px;top:1654px">
    <svg width="44" height="44" viewBox="0 0 44 44"><rect x="4" y="12" width="24" height="18" fill="var(--navy)"/><path d="M28 17 H35 L40 24 V30 H28 Z" fill="var(--navy)"/><circle cx="12" cy="33" r="4" fill="var(--navy)" stroke="#fff" stroke-width="1.5"/><circle cx="33" cy="33" r="4" fill="var(--navy)" stroke="#fff" stroke-width="1.5"/></svg>
  </div>

  <div class="abs tablet"></div>
  <div class="abs tablet-screen" role="img" aria-label="Introductory video preview"></div>
  <div class="abs tablet-name">Meridian Shield</div>
  <div class="abs tablet-dot"></div>

  <div class="abs icon-circle green" style="left:798px;top:1504px">
    <svg width="44" height="44" viewBox="0 0 44 44"><circle cx="22" cy="15" r="8" fill="var(--green)"/><path d="M7 38 Q8 25 22 25 Q36 25 37 38 Z" fill="var(--green)"/></svg>
  </div>
  <div class="abs cov-item" style="left:904px;top:1502px">
    <h3>DIRECTORS AND OFFICERS<br>(D&amp;O)</h3>
    <p>Business insurance is a risk management tool that enables</p>
  </div>

  <div class="abs icon-circle green" style="left:798px;top:1654px">
    <svg width="44" height="44" viewBox="0 0 44 44" stroke="var(--green)" stroke-width="4" fill="none"><path d="M10 10 L34 34 M34 10 L10 34"/><path d="M9 18 V9 H18 M26 9 H35 V18 M35 26 V35 H26 M18 35 H9 V26" stroke-width="3.5"/></svg>
  </div>
  <div class="abs cov-item" style="left:904px;top:1662px">
    <h3>DIFFERENCE IN CONDITIONS</h3>
    <p>Business insurance is a risk management tool that enables</p>
  </div>
</section>

<section>
  <div class="abs contact"></div>
  <h2 class="abs contact-title">QUICK CONTACT</h2>
  <div class="abs map" role="img" aria-label="Street map showing the office location"></div>

  <div class="abs c-icon" style="left:481px;top:1909px">
    <svg width="18" height="18" viewBox="0 0 18 18"><path d="M9 1 C5 1 3 4 3 7 C3 11 9 17 9 17 C9 17 15 11 15 7 C15 4 13 1 9 1 Z" fill="#ddd"/><circle cx="9" cy="7" r="2.3" fill="var(--dark)"/></svg>
  </div>
  <p class="abs c-text" style="left:546px;top:1904px">1280 Harbor Lane, Suite 140<br>Coral Bay, FL 33010</p>

  <div class="abs c-icon" style="left:481px;top:1975px">
    <svg width="18" height="18" viewBox="0 0 18 18"><path d="M4 1 L7 5 L5 7 Q7 11 11 13 L13 11 L17 14 L15 17 Q6 16 1 3 Z" fill="#ddd"/></svg>
  </div>
  <p class="abs c-text" style="left:546px;top:1983px">(555) 014-2290</p>

  <div class="abs c-icon" style="left:481px;top:2035px">
    <svg width="18" height="18" viewBox="0 0 18 18"><rect x="1" y="4" width="16" height="11" fill="#ddd"/><path d="M1 4 L9 10 L17 4" stroke="var(--dark)" stroke-width="1.5" fill="none"/></svg>
  </div>
  <p class="abs c-text" style="left:546px;top:2043px">hello@meridianshield.example</p>

  <div class="abs field" style="top:1881px"><svg width="12" height="12" viewBox="0 0 12 12"><circle cx="6" cy="3.5" r="3" fill="#666"/><path d="M0 12 Q1 7 6 7 Q11 7 12 12 Z" fill="#666"/></svg>YOUR NAME</div>
  <div class="abs field" style="top:1925px"><svg width="12" height="12" viewBox="0 0 12 12"><rect x="3" y="0" width="6" height="12" rx="1" fill="#666"/><rect x="4.2" y="1.5" width="3.6" height="7.5" fill="#fff"/></svg>PHONE</div>
  <div class="abs field" style="top:1971px"><svg width="12" height="12" viewBox="0 0 12 12"><rect x="0" y="2" width="12" height="8" fill="#666"/><path d="M0 2 L6 7 L12 2" stroke="#fff" fill="none"/></svg>EMAIL ADDRESS</div>
  <div class="abs field msg" style="top:2013px"><svg width="12" height="12" viewBox="0 0 12 12"><path d="M1 11 L2 8 L9 1 L11 3 L4 10 Z" fill="#666"/></svg>MESSAGE</div>
  <div class="abs btn-send">SEND</div>
</section>

<footer>
  <div class="abs footer"></div>
  <p class="abs footer-text">Copyright 2016 meridianshield.example All Rights Reserved</p>
</footer>

</body>
</html>
```